Artsy 1 Page Website/Brochure for climate change investment company

We want art like feel similar to https://velmora.quintrel.net/ for a 1 page online website (1 page) to have an online presence. We want to show credibility, no functionality. The only call to action is an email to the company.
3 sections 1) Company 2) Services, 3) brands.
The idea is 1) we are credible and serious, 2) market is increasing, 3) knowledge about sector, 4) large branded companies in the sector.
We want users to be interested and want to learn more.
There should be 1 or 2 animated sections. 1) GHG (green house gases) floating up or something showing emissions rising, 2) Services can scroll or loop.
See my mockup. The font should be standardized. The text shapes should be same. Keep same color palette unless you have better idea.
https://slides.brovanta.com/deck/7KxQ2mPzT9wLbV4nRfYcHd8sJuA6eGtNqXoZ1iMvBkE/view?ref=share
Logo for company AirLedgerHub.com

Target Market(s)

Potential Investors and Academics and Industry specialist. This is not for general consumers

Industry/Entity Type

Environment/Investors

Number of Pages Required

1 page

Requirements
Must have
• Artsy feel like a brochure
Should not have
• I do not want a functional website with lots of standard menus e.g. menus at the top

```html
<!DOCTYPE html>
<html lang="en">
<head>
<meta charset="utf-8">
<title>AirLedger Hub</title>
<link rel="stylesheet" href="https://fonts.googleapis.com/css2?family=Alegreya+Sans:wght@500;700;800&display=swap">
<style>
  :root{
    --page-purple:#5f1a9f;
    --brand-pink:#c4004f;
    --white:#ffffff;
    --forest-deep:#1f3a2a;
    --forest-mid:#3d5e34;
    --services-dark:#2a1a2a;
    --services-violet:#4a1a6e;
    --tile:#2e2a30;
    --space-dark:#232a2c;
    --logo-grey:#8d9396;
    --logo-line:#4a5154;
  }
  *{box-sizing:border-box;margin:0;padding:0}
  html,body{width:1200px;height:2256px;overflow:hidden}
  body{background:var(--page-purple);font-family:"Alegreya Sans",sans-serif;color:var(--white);position:relative}

  .panel{position:absolute;left:27px;width:1149px;height:698px;overflow:hidden;box-shadow:0 10px 30px rgba(0,0,0,.3)}

  /* Company */
  .company{top:30px}
  .company-sidebar{position:absolute;left:0;top:0;width:232px;height:100%;background:var(--brand-pink)}
  .brand-name{position:absolute;left:18px;top:50px;font-size:31px;font-weight:700;white-space:nowrap}
  .gas-pill{position:absolute;left:31px;width:172px;height:44px;border:1.5px solid var(--white);border-radius:22px;
    display:flex;align-items:center;justify-content:center;font-size:20px;font-weight:500}
  .gas-pill sub{font-size:11px;margin-left:2px;vertical-align:-4px}
  .contact{position:absolute;left:18px;top:652px;display:flex;align-items:center;gap:8px;font-size:13.5px;font-weight:700}
  .hero-photo{position:absolute;left:232px;top:0;right:0;bottom:0;
    background:radial-gradient(ellipse at 45% 50%,#3b5248 0%,var(--forest-mid) 40%,var(--forest-deep) 100%)}
  .hero-title{position:absolute;left:232px;right:0;top:280px;text-align:center;font-size:112px;font-weight:500;letter-spacing:1px}

  /* Services */
  .services{top:769px;background:linear-gradient(100deg,var(--services-dark) 0%,#2e1830 45%,var(--services-violet) 100%)}
  .section-title{position:absolute;left:0;right:0;text-align:center;font-size:72px;font-weight:800}
  .services .section-title{top:45px}
  .service-tile{position:absolute;width:205px;height:205px;background:var(--tile);opacity:.92;
    display:flex;align-items:center;justify-content:center;text-align:center;font-size:17px;font-weight:700;line-height:1.45;padding:0 8px}
  .service-tile.is-active{box-shadow:0 0 14px rgba(196,0,79,.6)}
  .service-tile.is-active span{width:180px;height:180px;border-radius:50%;background:var(--brand-pink);display:flex;align-items:center;justify-content:center}
  .node{position:absolute;border-radius:50%;background:rgba(255,255,255,.45)}

  /* Our Space */
  .our-space{top:1508px;background:var(--space-dark)}
  .our-space .section-title{top:120px}
  .partner{position:absolute;width:207px;height:83px;border:1.5px solid var(--logo-line);
    display:flex;align-items:center;justify-content:center;gap:9px;color:var(--logo-grey);font-size:25px;font-weight:700}
  .partner .mark{width:22px;height:22px;border-radius:50%;background:var(--logo-grey)}
  .deco{position:absolute}
</style>
</head>
<body>

<section class="panel company">
  <div class="hero-photo" role="img" aria-label="Aerial view of a dense forest with drifting clouds and a water drop at the centre"></div>
  <div class="hero-title">GHGs</div>
  <aside class="company-sidebar">
    <div class="brand-name">AirLedger Hub</div>
    <div class="gas-pill" style="top:265px">Co<sub>2</sub></div>
    <div class="gas-pill" style="top:327px">GHG</div>
    <div class="gas-pill" style="top:389px">CH<sub>4</sub></div>
    <div class="contact">
      <svg width="15" height="11" viewBox="0 0 15 11"><rect width="15" height="11" rx="1" fill="#fff"/><path d="M0.5 1 L7.5 6 L14.5 1" stroke="#c4004f" stroke-width="1.4" fill="none"/></svg>
      Partners@AirLedgerHub.com
    </div>
  </aside>
</section>

<section class="panel services">
  <span class="node" style="left:180px;top:90px;width:22px;height:22px"></span>
  <span class="node" style="left:88px;top:300px;width:22px;height:22px"></span>
  <span class="node" style="left:910px;top:73px;width:22px;height:22px"></span>
  <span class="node" style="left:1078px;top:93px;width:16px;height:16px"></span>
  <span class="node" style="left:1000px;top:280px;width:22px;height:22px"></span>
  <span class="node" style="left:1118px;top:562px;width:16px;height:16px"></span>
  <span class="node" style="left:1008px;top:658px;width:12px;height:12px"></span>
  <span class="node" style="left:92px;top:660px;width:12px;height:12px"></span>
  <div class="section-title">Services</div>
  <div class="service-tile" style="left:144px;top:192px">Carbon Capture</div>
  <div class="service-tile is-active" style="left:363px;top:192px"><span>Nature Based Solutions</span></div>
  <div class="service-tile" style="left:582px;top:192px">Technology based solutions</div>
  <div class="service-tile" style="left:801px;top:192px">Permanent Carbon<br>Removal</div>
  <div class="service-tile" style="left:144px;top:413px">New Methodologies</div>
  <div class="service-tile" style="left:363px;top:413px">REDD+</div>
  <div class="service-tile" style="left:582px;top:413px">Streaming</div>
  <div class="service-tile" style="left:801px;top:413px">Carbon Markets</div>
</section>

<section class="panel our-space">
  <svg class="deco" style="left:20px;top:28px" width="175" height="140" viewBox="0 0 175 140">
    <rect x="20" y="20" width="78" height="78" fill="#c4004f" transform="rotate(45 59 59)"/>
    <rect x="75" y="42" width="80" height="80" fill="none" stroke="#fff" stroke-width="1.5" transform="rotate(45 115 82)"/>
  </svg>
  <svg class="deco" style="left:988px;top:32px" width="80" height="46" viewBox="0 0 80 46">
    <circle cx="10" cy="36" r="7" fill="#c4004f"/><circle cx="35" cy="24" r="10" fill="#c4004f"/><circle cx="61" cy="13" r="13" fill="#c4004f"/>
  </svg>
  <div class="section-title">Our Space</div>

  <div class="partner" style="left:138px;top:237px">Terranex</div>
  <div class="partner" style="left:360px;top:237px;font-size:19px"><span class="mark"></span>Carbonwell</div>
  <div class="partner" style="left:582px;top:237px">Norvale Inc.</div>
  <div class="partner" style="left:804px;top:237px">Tradlet</div>

  <div class="partner" style="left:138px;top:343px">Kelmont</div>
  <div class="partner" style="left:360px;top:343px"><span class="mark"></span>Meridia</div>
  <div class="partner" style="left:582px;top:343px">Aurel Registry</div>
  <div class="partner" style="left:804px;top:343px;font-size:19px"><span class="mark" style="border-radius:0"></span>Continental Bureau</div>

  <div class="partner" style="left:138px;top:449px">Solvar Panel</div>
  <div class="partner" style="left:360px;top:449px">Paylane</div>
  <div class="partner" style="left:582px;top:449px">Voltrix</div>
  <div class="partner" style="left:804px;top:449px;font-size:34px">Searchly</div>

  <svg class="deco" style="left:52px;top:585px" width="48" height="22" viewBox="0 0 48 22">
    <circle cx="10" cy="11" r="8" fill="none" stroke="#fff" stroke-width="1.5"/>
    <circle cx="23" cy="11" r="8" fill="none" stroke="#fff" stroke-width="1.5"/>
    <circle cx="36" cy="11" r="8" fill="none" stroke="#fff" stroke-width="1.5"/>
  </svg>
  <svg class="deco" style="left:1050px;top:600px" width="80" height="65" viewBox="0 0 80 65">
    <rect x="10" y="15" width="30" height="30" fill="#c4004f" transform="rotate(45 25 30)"/>
    <rect x="32" y="20" width="32" height="32" fill="none" stroke="#fff" stroke-width="1.5" transform="rotate(45 48 36)"/>
  </svg>
</section>

</body>
</html>
```